BRISKEL Need a luxury modern business card designed.

Need a luxury modern business card designed. refer to the uploaded files for the company name and logo in the zip file under source files. i will making my descion on monday. so please send in before then so if we need to edit we will have the time. we have a trade show coming up and im on a deadline for printer.

Target Market(s)

high end clients

Contact Information for Business Card

Company nAme and logo. Tobias Fennick Co-Founder / Project Manager Office # 555-318-7094 Cell # 555-642-1586 BRISKEL.CA Tobias@briskel-example.ca

Font styles to use
Other font styles liked:
• Modern

Requirements
Must have
• Company name and logo, contact info, using the black, gold and white color scheme.

```html
<!DOCTYPE html>
<html lang="en">
<head>
<meta charset="utf-8">
<title>BRISKEL – Business Card</title>
<link rel="stylesheet" href="https://fonts.googleapis.com/css2?family=Poppins:wght@300;400;500&display=swap">
<style>
  :root {
    --backdrop: #1b1b1e;
    --card: #1f2022;
    --white: #f4f2ee;
    --gold: #b09a63;
    --grey: #8d8c88;
  }
  * { box-sizing: border-box; margin: 0; padding: 0; }
  html, body {
    width: 1200px; height: 800px; overflow: hidden;
    background: var(--backdrop);
    font-family: "Poppins", sans-serif;
    color: var(--white);
  }
  .canvas { position: relative; width: 1200px; height: 800px; }

  .card {
    position: absolute; top: 250px;
    width: 520px; height: 300px;
    background: var(--card);
    box-shadow: 0 18px 40px rgba(0,0,0,.55);
    overflow: hidden;
  }
  .card--front { left: 50px; }
  .card--back { left: 630px; }

  /* company name */
  .wordmark {
    position: absolute;
    display: flex; align-items: center; gap: 12px;
    font-weight: 400; letter-spacing: 2px; color: var(--white);
    line-height: 1; white-space: nowrap;
  }
  .wordmark__square { width: 12px; height: 12px; background: var(--gold); flex: none; }
  .card--front .wordmark { left: 50%; top: 50%; transform: translate(-50%, -50%); font-size: 44px; }
  .card--back .wordmark { right: 40px; top: 60px; font-size: 32px; }
  .card--back .wordmark__square { width: 10px; height: 10px; }

  /* person */
  .person { position: absolute; left: 36px; top: 166px; }
  .person__name { font-size: 20px; font-weight: 500; letter-spacing: .5px; text-transform: uppercase; line-height: 1.2; }
  .person__name .surname { color: var(--gold); }
  .person__role { font-size: 11px; color: var(--grey); font-weight: 300; margin-top: 3px; }
  .person__rule { width: 90px; height: 1px; background: var(--white); margin-top: 10px; }

  /* contacts */
  .contacts {
    position: absolute; left: 36px; right: 24px; bottom: 24px;
    display: flex; align-items: center; gap: 13px;
    font-size: 10px; font-weight: 400;
  }
  .contacts__group { display: flex; flex-direction: column; gap: 6px; font-style: normal; }
  .contacts__divider { width: 1px; height: 30px; background: var(--gold); flex: none; }
  .contact-line { display: flex; align-items: center; gap: 6px; white-space: nowrap; }
  .contact-line svg { width: 10px; height: 10px; flex: none; }
  .contacts__address span { white-space: nowrap; }

  .gold-band { position: absolute; left: 0; right: 0; bottom: 0; height: 4px; background: var(--gold); }
</style>
</head>
<body>
<main class="canvas">

  <section class="card card--front" aria-label="Card front">
    <div class="wordmark"><span class="wordmark__square"></span>BRISKEL</div>
  </section>

  <section class="card card--back" aria-label="Card back">
    <div class="wordmark"><span class="wordmark__square"></span>BRISKEL</div>

    <div class="person">
      <h1 class="person__name">Tobias <span class="surname">Fennick</span></h1>
      <p class="person__role">Co-Founder / Project Manager</p>
      <div class="person__rule"></div>
    </div>

    <div class="contacts">
      <div class="contacts__group">
        <div class="contact-line">
          <svg viewBox="0 0 10 10" aria-hidden="true"><path d="M2 1 L4 1 L4.5 3 L3.4 3.8 Q4.2 5.6 6.2 6.6 L7 5.5 L9 6 L9 8 Q5 9 2.5 6 Q1 4 2 1 Z" fill="#b09a63"/></svg>
          555-318-7094
        </div>
        <div class="contact-line">
          <svg viewBox="0 0 10 10" aria-hidden="true"><rect x="2.5" y="0.5" width="5" height="9" rx="1" fill="none" stroke="#b09a63"/></svg>
          555-642-1586
        </div>
      </div>
      <span class="contacts__divider"></span>
      <div class="contacts__group">
        <div class="contact-line">
          <svg viewBox="0 0 10 10" aria-hidden="true"><circle cx="5" cy="5" r="4.2" fill="none" stroke="#b09a63"/><path d="M1 5 H9 M5 0.8 Q2.5 5 5 9.2 M5 0.8 Q7.5 5 5 9.2" fill="none" stroke="#b09a63" stroke-width=".7"/></svg>
          BRISKEL.CA
        </div>
        <div class="contact-line">
          <svg viewBox="0 0 10 10" aria-hidden="true"><rect x="0.5" y="2" width="9" height="6" fill="#b09a63"/><path d="M0.5 2 L5 5.5 L9.5 2" fill="none" stroke="#1f2022" stroke-width=".8"/></svg>
          Tobias@briskel-example.ca
        </div>
      </div>
      <span class="contacts__divider"></span>
      <address class="contacts__group contacts__address">
        <span>48 Harlow Lane, Unit 7,</span>
        <span>Ridgemont, ON. K0A 2X9</span>
      </address>
    </div>

    <div class="gold-band"></div>
  </section>

</main>
</body>
</html>
```